Business card for law firm

Need business card for new law firm. Think confident, authoritative, conservative, but not stuffy or old-fashioned.

Contact Information for Business Card

Content for card - logo (uploaded), plus the following:

Paul Whitcombe (larger font)
Managing Partner (larger font, but not as large as name)
Level 9, 7 Ferris Lane
Sydney NSW 2000
Main Tel 02 9364 2710
Direct Tel 02 8472 3159
Email paul@qvlegal.com.au
www.qvlegal.com.au

Letterhead design should include logo plus:
Level 9, 7 Ferris Lane
Sydney NSW 2000
Tel 02 8472 3159
www.qvlegal.com.au

```html
<!DOCTYPE html>
<html lang="en">
<head>
<meta charset="utf-8">
<title>Quayvale Lawyers — Business Card</title>
<link rel="stylesheet" href="https://fonts.googleapis.com/css2?family=Roboto:wght@400;500;700&family=Open+Sans:wght@400;600&display=swap">
<style>
  :root {
    --navy: #0b1d57;
    --navy-deep: #0a1b52;
    --ink: #1e1e1e;
    --grey: #5f5f5f;
    --grey-strong: #4e4e4e;
    --paper: #ffffff;
    --backdrop: #dcdcdc;
  }
  * { margin: 0; padding: 0; box-sizing: border-box; }
  html, body {
    width: 1146px;
    height: 1200px;
    overflow: hidden;
    background: var(--backdrop);
  }
  .canvas {
    position: relative;
    width: 1146px;
    height: 1200px;
  }
  .card {
    position: absolute;
    left: 206px;
    width: 732px;
    height: 423px;
    overflow: hidden;
  }
  .card--front { top: 125px; background: var(--paper); }
  .card--back  { top: 654px; background: var(--navy-deep); }

  /* Brand block */
  .brand {
    position: absolute;
    left: 29px;
    top: 119px;
    width: 295px;
    text-align: center;
  }
  .brand__square {
    display: block;
    width: 64px;
    height: 64px;
    margin: 0 auto 26px;
    background: var(--navy);
  }
  .brand__name {
    font-family: "Roboto", sans-serif;
    font-weight: 500;
    font-size: 24px;
    letter-spacing: 2px;
    text-transform: uppercase;
    color: var(--navy);
    white-space: nowrap;
  }

  /* Contact details */
  .details {
    position: absolute;
    left: 416px;
    top: 98px;
  }
  .details__name {
    font-family: "Roboto", sans-serif;
    font-weight: 700;
    font-size: 35px;
    line-height: 38px;
    color: var(--navy);
    white-space: nowrap;
  }
  .details__role {
    font-family: "Roboto", sans-serif;
    font-weight: 500;
    font-size: 22px;
    line-height: 26px;
    color: var(--ink);
  }
  .details__group {
    margin-top: 14px;
    font-family: "Open Sans", sans-serif;
    font-size: 17px;
    line-height: 21.5px;
    color: var(--grey);
  }
  .details__group--phones { margin-top: 12px; }
  .details__web {
    margin-top: 12px;
    font-family: "Open Sans", sans-serif;
    font-weight: 600;
    font-size: 18px;
    color: var(--grey-strong);
  }

  .card__band {
    position: absolute;
    left: 0;
    bottom: 0;
    width: 100%;
    height: 21px;
    background: var(--navy);
  }

  .card__corner-square {
    position: absolute;
    left: 612px;
    top: 300px;
    width: 72px;
    height: 72px;
    background: rgba(255, 255, 255, 0.88);
  }
</style>
</head>
<body>
<div class="canvas">
  <section class="card card--front" aria-label="Business card front">
    <div class="brand">
      <span class="brand__square" aria-hidden="true"></span>
      <div class="brand__name">Quayvale Lawyers</div>
    </div>

    <div class="details">
      <div class="details__name">Paul Whitcombe</div>
      <div class="details__role">Managing Partner</div>
      <div class="details__group">
        <div>Level 9, 7 Ferris Lane</div>
        <div>Sydney NSW 2000</div>
      </div>
      <div class="details__group details__group--phones">
        <div>02 9364 2710 (Main)</div>
        <div>02 8472 3159 (Direct)</div>
        <div>paul@qvlegal.com.au</div>
      </div>
      <div class="details__web">www.qvlegal.com.au</div>
    </div>

    <div class="card__band"></div>
  </section>

  <section class="card card--back" aria-label="Business card back">
    <span class="card__corner-square" aria-hidden="true"></span>
  </section>
</div>
</body>
</html>
```